New hardcover book cover

I want a striking, eye-catching cover with title, subtitle and a picture.See for previous book covers: www.brightquillpress.com

Target Market(s)

young, successful entrepreneurs that have built a business in a niche market that they discovered.

Font styles to use
Serif

Colors

Designer to choose colors to be used in the design.

Requirements
Must have
• A book cover that impresses and captures the imagination of those who look at it.
• MY MISTAKE, SORRY.
• Title: Founders Behind the Quiet Trade Boom
• Subtitle: 25 stories of success from
• discovering hidden opportunities
• Author: Dennis Harlow
• Please use the photo attached, thanks.

```html
<!DOCTYPE html>
<html lang="en">
<head>
<meta charset="utf-8">
<title>Founders Behind the Quiet Trade Boom — Dennis Harlow</title>
<link href="https://fonts.googleapis.com/css2?family=Cinzel:wght@400;500&family=Marcellus&display=swap" rel="stylesheet">
<style>
  :root {
    --stage: #262626;
    --navy: #111a4a;
    --photo-deep: #1d2e8a;
    --photo-mid: #3f5fcf;
    --photo-light: #8fa8ee;
    --white: #f4f4f8;
    --muted: #c9cde6;
    --pink: #ee3f7a;
  }
  html, body {
    margin: 0;
    width: 1200px;
    height: 905px;
    overflow: hidden;
    background: var(--stage);
  }
  .book-cover {
    position: absolute;
    left: 320px;
    top: 20px;
    width: 560px;
    height: 865px;
    background: var(--navy);
    overflow: hidden;
  }
  .cover-photo {
    position: absolute;
    left: 0;
    top: 0;
    width: 560px;
    height: 430px;
    background:
      radial-gradient(ellipse at 75% 70%, var(--photo-light) 0%, transparent 55%),
      linear-gradient(90deg, var(--photo-deep) 0%, var(--photo-mid) 45%, var(--photo-light) 100%);
  }
  .photo-accent {
    position: absolute;
    right: 0;
    top: 428px;
    width: 168px;
    height: 5px;
    background: var(--pink);
  }
  .author-name {
    position: absolute;
    left: 92px;
    top: 36px;
    margin: 0;
    font-family: "Marcellus", serif;
    font-weight: 400;
    font-size: 36px;
    letter-spacing: 5px;
    color: var(--white);
    text-transform: uppercase;
  }
  .book-title {
    position: absolute;
    left: 0;
    top: 500px;
    width: 560px;
    margin: 0;
    text-align: center;
    font-family: "Cinzel", serif;
    font-weight: 400;
    line-height: 1;
    text-transform: uppercase;
  }
  .title-line { display: block; }
  .title-lead { color: var(--white); font-size: 44px; }
  .title-middle {
    display: flex;
    justify-content: center;
    align-items: flex-end;
    gap: 8px;
    color: var(--white);
    margin-top: 2px;
  }
  .title-small {
    display: flex;
    flex-direction: column;
    align-items: center;
    font-size: 24px;
    line-height: 0.95;
    padding-bottom: 6px;
  }
  .title-big { font-size: 62px; }
  .title-accent { color: var(--pink); font-size: 64px; margin-top: -2px; }
  .book-subtitle {
    position: absolute;
    left: 0;
    top: 772px;
    width: 560px;
    margin: 0;
    text-align: center;
    font-family: "Marcellus", serif;
    font-size: 19px;
    line-height: 1.4;
    letter-spacing: 1px;
    color: var(--muted);
  }
  .book-subtitle span { display: block; }
</style>
</head>
<body>
  <div class="book-cover">
    <div class="cover-photo" role="img" aria-label="Close-up photograph of darts with patterned flights lodged in a dartboard, in blue tones"></div>
    <div class="photo-accent"></div>
    <p class="author-name">Dennis Harlow</p>
    <h1 class="book-title">
      <span class="title-line title-lead">Founders</span>
      <span class="title-line title-middle">
        <span class="title-small"><span>Behind</span><span>the</span></span>
        <span class="title-big">Quiet</span>
      </span>
      <span class="title-line title-accent">Trade</span>
      <span class="title-line title-accent">Boom</span>
    </h1>
    <p class="book-subtitle">
      <span>25 stories of success from</span>
      <span>discovering hidden opportunities</span>
    </p>
  </div>
</body>
</html>
```